Mastering Modern Vineyard Management

size of the ad - 8”x 10.75" plus 0.25" bleed
I would like an ad for a magazine that will stand out and make people want to read the ad.
The ad should not be crowded and people reading the ad will be able to read the text.
I would like it to be a creative and modern-day design.
the list of topics should not be the focus of the ad.
the text is attached.
If you decide to use people in the ad then please no ladies.
please note that leave over 1 inch for the bottom of the footer

```html
<!DOCTYPE html>
<html lang="en">
<head>
<meta charset="utf-8">
<title>Vineyard Course – Mastering Modern Vineyard Management</title>
<link rel="stylesheet" href="https://fonts.googleapis.com/css2?family=Anton&family=Montserrat:wght@500;600;700;800&family=Oswald:wght@300;400;600&display=swap">
<style>
  :root {
    --navy: #0f3461;
    --navy-deep: #0b2a50;
    --sky: #4ea6ec;
    --yellow: #f7d417;
    --orange: #e03c0f;
    --blue: #1565c0;
    --ink: #123a6b;
    --paper: #ffffff;
    --backdrop: #e7e5e2;
    --white: #ffffff;
  }
  * { box-sizing: border-box; margin: 0; padding: 0; }
  html, body { width: 1200px; height: 800px; overflow: hidden; }
  body {
    background: var(--backdrop);
    display: flex; align-items: center; justify-content: center;
    font-family: "Montserrat", sans-serif;
  }
  .flyer {
    position: relative;
    width: 580px; height: 760px;
    background: var(--paper);
    box-shadow: 0 6px 24px rgba(0,0,0,.18);
    overflow: hidden;
  }
  .hero {
    position: absolute; left: 0; top: 0; width: 100%; height: 440px;
    background: var(--navy);
  }
  .course-title {
    position: absolute; top: 34px; left: 0; width: 100%;
    text-align: center;
    font-family: "Anton", sans-serif; font-weight: 400; font-size: 58px; letter-spacing: 1.5px;
    line-height: 1.1;
    color: var(--yellow);
  }
  .hero-art {
    position: absolute; left: 60px; top: 118px; width: 460px; height: 232px;
    background: linear-gradient(180deg, #eef1f8 0%, #9fb0cc 100%);
    border-radius: 4px;
  }
  .hero-rule {
    position: absolute; left: 40px; right: 40px; top: 360px; height: 1.5px;
    background: var(--white); opacity: .8;
  }
  .program-name {
    position: absolute; top: 372px; left: 0; width: 100%; text-align: center;
    font-weight: 800; font-size: 20px; line-height: 1.2; color: var(--sky); letter-spacing: .2px;
  }
  .tagline {
    position: absolute; top: 404px; left: 0; width: 100%; text-align: center;
    font-weight: 600; font-size: 13px; line-height: 1.2; color: var(--white); letter-spacing: 1.2px;
  }
  .details-band {
    position: absolute; left: 0; top: 440px; width: 100%; height: 68px;
    background: var(--orange);
    display: flex; align-items: center; justify-content: center; gap: 18px;
    color: var(--yellow);
  }
  .band-divider { width: 1.5px; height: 44px; background: rgba(255,255,255,.7); }
  .location {
    font-family: "Oswald", sans-serif; font-weight: 400; font-size: 42px; letter-spacing: .5px; line-height: 1;
  }
  .sessions { display: flex; align-items: center; gap: 6px; }
  .sessions-count { font-family: "Oswald", sans-serif; font-weight: 400; font-size: 44px; line-height: 1; }
  .sessions-text { display: flex; flex-direction: column; line-height: 1; }
  .sessions-day { font-family: "Oswald", sans-serif; font-weight: 300; font-size: 26px; }
  .sessions-note { font-weight: 700; font-size: 9.5px; letter-spacing: .5px; margin-top: 3px; }
  .start { display: flex; flex-direction: column; line-height: 1.05; }
  .start-date { font-family: "Oswald", sans-serif; font-weight: 300; font-size: 22px; }
  .start-offer { font-weight: 800; font-size: 12.5px; color: var(--white); letter-spacing: .3px; }
  .scholarships {
    position: absolute; top: 530px; left: 0; width: 100%; text-align: center;
    font-weight: 800; font-size: 19px; line-height: 1.2; color: var(--blue);
  }
  .audience {
    position: absolute; top: 558px; left: 0; width: 100%; text-align: center;
    font-weight: 800; font-size: 16px; line-height: 1.2; color: var(--ink);
  }
  .topics-box {
    position: absolute; left: 34px; right: 34px; top: 604px; height: 106px;
    border: 1.5px solid var(--blue); border-radius: 8px;
  }
  .topics-label {
    position: absolute; top: -1px; left: 50%; transform: translateX(-50%);
    background: var(--blue); color: var(--white);
    font-weight: 700; font-size: 11px; letter-spacing: .4px;
    padding: 5px 22px 6px; border-radius: 0 0 8px 8px; white-space: nowrap;
  }
  .topics-list {
    position: absolute; top: 32px; left: 18px; right: 14px;
    display: grid; grid-template-columns: 1fr 1.15fr 1fr; gap: 10px;
  }
  .topics-column { list-style: none; }
  .topics-column li {
    display: flex; align-items: flex-start; gap: 5px;
    font-weight: 500; font-size: 10.5px; color: var(--ink); line-height: 1.3;
    margin-bottom: 3px;
  }
  .tick { flex: none; width: 10px; height: 10px; margin-top: 2px; }
</style>
</head>
<body>
  <main class="flyer">
    <section class="hero">
      <h1 class="course-title">VINEYARD COURSE</h1>
      <div class="hero-art" role="img" aria-label="Illustration in white and navy tones showing the course theme"></div>
      <div class="hero-rule"></div>
      <h2 class="program-name">MASTERING MODERN VINEYARD MANAGEMENT</h2>
      <p class="tagline">INVESTING IN KNOWLEDGE IS INVESTING IN OPPORTUNITIES</p>
    </section>

    <section class="details-band">
      <span class="location">REDFIELD</span>
      <span class="band-divider"></span>
      <div class="sessions">
        <span class="sessions-count">10</span>
        <div class="sessions-text">
          <span class="sessions-day">TUESDAY</span>
          <span class="sessions-note">EVENINGS SESSIONS</span>
        </div>
      </div>
      <span class="band-divider"></span>
      <div class="start">
        <span class="start-date">STARTING FEB.28</span>
        <span class="start-offer">EARLY BIRD SPECIAL</span>
      </div>
    </section>

    <p class="scholarships">LIMITED PARTIAL SCHOLARSHIPS</p>
    <p class="audience">For those that started or would like to go into vineyards</p>

    <section class="topics-box">
      <span class="topics-label">TOPICS: PARTIAL LISTING</span>
      <div class="topics-list">
        <ul class="topics-column">
          <li><svg class="tick" viewBox="0 0 10 10"><circle cx="5" cy="5" r="5" fill="#1565c0"/><path d="M2.7 5.2l1.6 1.6 3-3.2" stroke="#fff" stroke-width="1.3" fill="none"/></svg>Vineyard investment strategies</li>
          <li><svg class="tick" viewBox="0 0 10 10"><circle cx="5" cy="5" r="5" fill="#1565c0"/><path d="M2.7 5.2l1.6 1.6 3-3.2" stroke="#fff" stroke-width="1.3" fill="none"/></svg>Site assessment</li>
          <li><svg class="tick" viewBox="0 0 10 10"><circle cx="5" cy="5" r="5" fill="#1565c0"/><path d="M2.7 5.2l1.6 1.6 3-3.2" stroke="#fff" stroke-width="1.3" fill="none"/></svg>Financing</li>
        </ul>
        <ul class="topics-column">
          <li><svg class="tick" viewBox="0 0 10 10"><circle cx="5" cy="5" r="5" fill="#1565c0"/><path d="M2.7 5.2l1.6 1.6 3-3.2" stroke="#fff" stroke-width="1.3" fill="none"/></svg>Soil and water</li>
          <li><svg class="tick" viewBox="0 0 10 10"><circle cx="5" cy="5" r="5" fill="#1565c0"/><path d="M2.7 5.2l1.6 1.6 3-3.2" stroke="#fff" stroke-width="1.3" fill="none"/></svg>Canopy management</li>
          <li><svg class="tick" viewBox="0 0 10 10"><circle cx="5" cy="5" r="5" fill="#1565c0"/><path d="M2.7 5.2l1.6 1.6 3-3.2" stroke="#fff" stroke-width="1.3" fill="none"/></svg>Vineyard legal basics</li>
          <li><svg class="tick" viewBox="0 0 10 10"><circle cx="5" cy="5" r="5" fill="#1565c0"/><path d="M2.7 5.2l1.6 1.6 3-3.2" stroke="#fff" stroke-width="1.3" fill="none"/></svg>Harvest planning</li>
        </ul>
        <ul class="topics-column">
          <li><svg class="tick" viewBox="0 0 10 10"><circle cx="5" cy="5" r="5" fill="#1565c0"/><path d="M2.7 5.2l1.6 1.6 3-3.2" stroke="#fff" stroke-width="1.3" fill="none"/></svg>Pest control</li>
          <li><svg class="tick" viewBox="0 0 10 10"><circle cx="5" cy="5" r="5" fill="#1565c0"/><path d="M2.7 5.2l1.6 1.6 3-3.2" stroke="#fff" stroke-width="1.3" fill="none"/></svg>Dealing with wineries</li>
          <li><svg class="tick" viewBox="0 0 10 10"><circle cx="5" cy="5" r="5" fill="#1565c0"/><path d="M2.7 5.2l1.6 1.6 3-3.2" stroke="#fff" stroke-width="1.3" fill="none"/></svg>Tax fundamentals</li>
        </ul>
      </div>
    </section>
  </main>
</body>
</html>
```